Publishing House

Amber Heron
Exotic, they weave silk out of nowhere. Blessed with a keen sense. Sophisticated discernment. Fearsome reputation. Powerful, but do not harm. Unless, you really needle them. Believe in continuous improvement. A young tarantula may shed its exoskeleton periodically in order to grow, a process called molting : several times a year as a part of the maturation process.
White. The colour pristine. Everything pure. Blemish-free. We feel for the writer. We want to infuse spurt of purity into publishing.
We, at Amber Heron Publishing, are here to question the status-quo, to provide a fresh, invigorating platform for writers to reach their art to their readership via processes that are transparent, impartial and non-discriminatory, and a level of transparency that will set new benchmarks in the world of publishing.
We bring to you new concepts in the areas of editing, proof-reading and cover-designing. Our suite of marketing services targets new, and web-based methods as well as traditional methods.
It is time the writer got his or her due!

I have attached our logo also

Industry/Entity Type

House

```html
<!DOCTYPE html>
<html lang="en">
<head>
<meta charset="utf-8">
<title>Amber Heron Publishing — Page Cover</title>
<link rel="stylesheet" href="https://fonts.googleapis.com/css2?family=Righteous&family=Cinzel:wght@600&display=swap">
<style>
  :root {
    --page-bg: #eef0f4;
    --parchment-light: #f6e2b4;
    --parchment-mid: #e8c68c;
    --parchment-dark: #c9924e;
    --shelf-light: #efe6d6;
    --shelf-mid: #d8c7ad;
    --shelf-warm: #b98a5c;
    --headline: #5b2c0e;
    --mark-gold: #d8ae62;
    --mark-gold-soft: rgba(190, 130, 60, 0.45);
    --avatar-bg: #1f1b1b;
    --avatar-frame: #ffffff;
    --avatar-border: #b8bcc6;
  }

  * { box-sizing: border-box; margin: 0; padding: 0; }

  html, body {
    width: 1200px;
    height: 718px;
    overflow: hidden;
    background: var(--page-bg);
  }

  .canvas {
    position: relative;
    width: 1200px;
    height: 718px;
  }

  .cover {
    position: absolute;
    left: 30px;
    top: 118px;
    width: 1140px;
    height: 422px;
    overflow: hidden;
    background:
      radial-gradient(ellipse at 30% 40%, var(--parchment-light) 0%, var(--parchment-mid) 55%, var(--parchment-dark) 100%);
  }

  .cover-photo {
    position: absolute;
    left: 540px;
    top: 0;
    width: 600px;
    height: 422px;
    background:
      linear-gradient(90deg, rgba(232, 198, 140, 1) 0%, rgba(232, 198, 140, 0) 22%),
      linear-gradient(180deg, var(--shelf-light) 0%, var(--shelf-mid) 60%, var(--shelf-warm) 100%);
  }

  .cover-mark {
    position: absolute;
    left: 90px;
    top: 96px;
    width: 340px;
    text-align: center;
    font-family: "Cinzel", serif;
    font-weight: 600;
    font-size: 38px;
    letter-spacing: 2px;
    color: var(--mark-gold-soft);
  }

  .headline {
    position: absolute;
    left: 287px;
    top: 258px;
    font-family: "Righteous", sans-serif;
    font-size: 38px;
    line-height: 49px;
    letter-spacing: 1px;
    text-transform: uppercase;
    color: var(--headline);
  }

  .avatar {
    position: absolute;
    left: 61px;
    top: 376px;
    width: 224px;
    height: 224px;
    padding: 7px;
    background: var(--avatar-frame);
    border: 1px solid var(--avatar-border);
    border-radius: 3px;
  }

  .avatar-inner {
    width: 100%;
    height: 100%;
    background: var(--avatar-bg);
    display: flex;
    align-items: center;
    justify-content: center;
  }

  .avatar-name {
    font-family: "Cinzel", serif;
    font-weight: 600;
    font-size: 24px;
    letter-spacing: 1px;
    color: var(--mark-gold);
  }
</style>
</head>
<body>
  <main class="canvas">
    <section class="cover">
      <div class="cover-photo" role="img" aria-label="Photograph of a bright bookshop wall with cream shelves full of colourful books"></div>
      <div class="cover-mark">Amber Heron</div>
      <h1 class="headline">All publisher<br>solutions in<br>under one roof</h1>
    </section>

    <div class="avatar">
      <div class="avatar-inner">
        <span class="avatar-name">Amber Heron</span>
      </div>
    </div>
  </main>
</body>
</html>
```